Dunmore Roofing

Want a professional looking business card

Industry/Entity Type

Business

Contact Information for Business Card

Paul Dunmore ( Owner) paul@dunmoreroofing-example.com, www.dunmoreroofing-example.com, Adress: 4172 Township road 43 Plantagenet,ON K9X4T2

```html
<!DOCTYPE html>
<html lang="en">
<head>
<meta charset="utf-8">
<title>Dunmore Roofing – Business Card</title>
<link rel="stylesheet" href="https://fonts.googleapis.com/css2?family=Open+Sans:wght@400;600&display=swap">
<style>
  :root {
    --page-bg: #e9e7e4;
    --card-bg: #0e0e0f;
    --text-light: #e6e6e6;
    --text-muted: #bdbdbd;
    --brand-blue: #2456a6;
    --rule-blue: #2a5cb0;
  }
  * { margin: 0; padding: 0; box-sizing: border-box; }
  html, body {
    width: 1200px;
    height: 844px;
    overflow: hidden;
    background: var(--page-bg);
    font-family: "Open Sans", Arial, sans-serif;
  }
  .sheet {
    width: 1200px;
    height: 844px;
    display: flex;
    align-items: center;
    justify-content: center;
    gap: 40px;
  }
  .card {
    width: 520px;
    height: 298px;
    background: var(--card-bg);
    border-radius: 3px;
    position: relative;
    box-shadow: 0 8px 24px rgba(0,0,0,0.25);
    color: var(--text-light);
  }

  /* Front */
  .brand-name {
    position: absolute;
    top: 58px;
    left: 0;
    right: 0;
    display: flex;
    align-items: center;
    justify-content: center;
    gap: 10px;
    font-weight: 600;
    font-size: 28px;
    letter-spacing: 0.5px;
    color: #ffffff;
  }
  .brand-square {
    width: 14px;
    height: 14px;
    background: var(--brand-blue);
  }
  .contact-list {
    position: absolute;
    left: 36px;
    top: 166px;
    list-style: none;
    font-size: 12.5px;
    line-height: 22px;
  }
  .contact-list li {
    display: flex;
    align-items: center;
    gap: 6px;
  }
  .contact-icon { width: 12px; height: 12px; flex: none; }
  .owner {
    position: absolute;
    left: 300px;
    top: 150px;
  }
  .owner-name {
    color: var(--brand-blue);
    font-size: 16px;
    font-weight: 400;
    letter-spacing: 0.3px;
    text-transform: uppercase;
  }
  .owner-title {
    font-size: 12px;
    color: var(--text-muted);
    margin-top: 2px;
  }
  .divider {
    position: absolute;
    left: 36px;
    right: 36px;
    top: 224px;
    height: 1px;
    background: var(--rule-blue);
  }
  .address {
    position: absolute;
    left: 36px;
    right: 36px;
    top: 234px;
    font-size: 12.5px;
    text-align: right;
  }

  /* Back */
  .card-back {
    display: flex;
    align-items: center;
    justify-content: center;
  }
  .back-brand {
    display: flex;
    align-items: center;
    gap: 12px;
    font-weight: 600;
    font-size: 32px;
    color: var(--brand-blue);
  }
  .back-brand .brand-square { width: 16px; height: 16px; }
</style>
</head>
<body>
<main class="sheet">
  <section class="card card-front" aria-label="Business card front">
    <div class="brand-name"><span class="brand-square"></span>Dunmore Roofing</div>

    <ul class="contact-list">
      <li>paul@dunmoreroofing-example.com
        <svg class="contact-icon" viewBox="0 0 12 12" aria-hidden="true">
          <rect width="12" height="12" rx="2" fill="#2456a6"/>
          <rect x="2" y="3.5" width="8" height="5" fill="none" stroke="#fff" stroke-width="0.9"/>
          <path d="M2 3.5 L6 6.5 L10 3.5" fill="none" stroke="#fff" stroke-width="0.9"/>
        </svg>
      </li>
      <li>www.dunmoreroofing-example.com
        <svg class="contact-icon" viewBox="0 0 12 12" aria-hidden="true">
          <circle cx="6" cy="6" r="6" fill="#2456a6"/>
          <circle cx="6" cy="6" r="3.6" fill="none" stroke="#fff" stroke-width="0.8"/>
          <ellipse cx="6" cy="6" rx="1.5" ry="3.6" fill="none" stroke="#fff" stroke-width="0.8"/>
          <line x1="2.4" y1="6" x2="9.6" y2="6" stroke="#fff" stroke-width="0.8"/>
        </svg>
      </li>
    </ul>

    <div class="owner">
      <p class="owner-name">Paul Dunmore</p>
      <p class="owner-title">Owner</p>
    </div>

    <div class="divider"></div>
    <p class="address">4172 Township road 43 Plantagenet,ON K9X4T2</p>
  </section>

  <section class="card card-back" aria-label="Business card back">
    <div class="back-brand"><span class="brand-square"></span>Dunmore Roofing</div>
  </section>
</main>
</body>
</html>
```